Redesign of Form/Document Navigation Page

I need a redesign of our document and navigation bar on the left. We want the same navigation bar layout/setup but want the buttons and typography to be simple and matching all over. The form needs to be aesthetically pleasing and fit within the page.

1st attachment is our Direct Deposit and the second is the form continued.

```html
<!DOCTYPE html>
<html lang="en">
<head>
<meta charset="utf-8">
<title>Employee Direct Deposit Enrollment Form</title>
<link href="https://fonts.googleapis.com/css2?family=Montserrat:wght@400;600;700&family=Open+Sans:wght@400;600;700&display=swap" rel="stylesheet">
<style>
:root{
  --page:#f2f2f2;
  --white:#ffffff;
  --navy:#1f4f8f;
  --blue:#2a5ea8;
  --gold:#f0b21c;
  --gold-dark:#e0a20f;
  --text:#222222;
  --muted:#555555;
  --line:#d4d4d4;
  --card-line:#e2e2e2;
  --link:#2b5a9c;
}
*{margin:0;padding:0;box-sizing:border-box}
html,body{width:1200px;height:1028px;overflow:hidden;background:var(--page);font-family:"Open Sans",Arial,sans-serif;color:var(--text)}
.canvas{position:relative;width:1200px;height:1028px;overflow:hidden}

/* header */
.site-header{position:absolute;left:0;top:0;width:1200px;height:75px;background:var(--white);border-bottom:1px solid #e4e4e4}
.brand{position:absolute;left:67px;top:22px;display:flex;align-items:center;gap:8px}
.brand-mark{width:28px;height:28px;border-radius:50%;background:var(--navy)}
.brand-name{font-family:"Open Sans",sans-serif;font-weight:700;font-size:16px;line-height:16px;color:var(--gold);width:140px}
.main-nav{position:absolute;left:291px;top:27px;display:flex;gap:16px;font-family:"Montserrat",sans-serif;font-size:12.5px;color:#333}
.header-divider{position:absolute;left:1024px;top:18px;width:1px;height:38px;background:#e4e4e4}
.user-menu{position:absolute;left:1045px;top:31px;font-size:10px;color:#444}
.user-menu::after{content:"";display:inline-block;margin-left:3px;border:3px solid transparent;border-top-color:#999;vertical-align:-1px}
.power-btn{position:absolute;left:1106px;top:23px;width:28px;height:28px;border-radius:50%;border:1px solid #ddd;background:#f6f6f6;display:flex;align-items:center;justify-content:center}

/* back button */
.back-btn{position:absolute;left:63px;top:90px;width:113px;height:28px;background:var(--blue);color:#fff;font-size:10px;font-weight:600;display:flex;align-items:center;justify-content:center;letter-spacing:.2px}

/* sidebar */
.side-nav{position:absolute;left:63px;top:134px;width:229px}
.nav-card{position:relative;height:107px;margin-bottom:8.5px;background:var(--white);border:2px solid var(--card-line);border-left:none}
.nav-card::before{content:"";position:absolute;left:0;top:-2px;bottom:-2px;width:47px;background:var(--gold)}
.nav-icon{position:absolute;left:13px;top:22px;width:62px;height:62px;border-radius:50%;background:var(--navy);border:2px solid var(--white)}
.nav-label{position:absolute;left:83px;top:0;bottom:0;display:flex;align-items:center;font-family:"Montserrat",sans-serif;font-size:13px;line-height:18px;color:#333}

/* form panel */
.form-panel{position:absolute;left:315px;top:134px;width:818px;height:799px;background:var(--white);border:1px solid var(--line);overflow:hidden}
.scrollbar{position:absolute;right:0;top:0;width:12px;height:100%;background:#f4f4f4;border-left:1px solid #e6e6e6}
.scrollbar .thumb{position:absolute;left:2px;top:10px;width:7px;height:195px;background:#c8c8c8}
.form-panel .el{position:absolute}
.form-title{left:0;width:805px;top:32px;text-align:center;font-family:"Montserrat",sans-serif;font-size:20.5px;color:var(--blue);font-weight:400}
.form-title strong{font-weight:700}
.intro{left:25px;width:765px;top:81px;font-size:9.7px;line-height:18.5px;color:var(--text)}
.intro-2{top:145px}
.attach-box{left:24px;top:186px;width:771px;height:132px;border:1px solid var(--line)}
.attach-link{left:0;width:100%;top:40px;text-align:center;font-size:9.5px;color:var(--link);text-decoration:underline}
.refresh-btn{left:335px;top:62px;width:100px;height:34px;background:var(--gold);border-bottom:2px solid var(--gold-dark);color:#fff;font-size:11px;font-weight:600;display:flex;align-items:center;justify-content:center;letter-spacing:.3px}
.section-title{left:25px;font-size:12.5px;font-weight:600;color:var(--text)}
.note{left:25px;font-size:9.7px;color:var(--text)}
.note-strong{font-size:10.5px;font-weight:600}
.radio-row{left:25px;display:flex;align-items:center;font-size:9.7px;color:var(--text)}
.radio{display:inline-flex;align-items:center;margin-right:30px}
.radio::before{content:"";width:9px;height:9px;border-radius:50%;border:1px solid #aaa;background:#f4f4f4;margin-right:7px}
.field-label{font-size:10px;color:var(--muted)}
.field{width:251px;height:31px;border:1px solid var(--line);background:#fff}
.amount-label{font-size:9.7px;color:var(--text)}
.amount-box{width:58px;height:24px;background:var(--gold);color:#fff;font-size:10px;display:flex;align-items:center;justify-content:center}
.legal{left:25px;width:765px;top:698px;font-size:9.7px;line-height:20.6px;color:var(--text)}

/* footer */
.footer-rule{position:absolute;left:66px;top:965px;width:1068px;height:1px;background:#dcdcdc}
.footer-links{position:absolute;left:66px;top:991px;font-size:9.7px;color:#333;display:flex;gap:9px}
.social{position:absolute;left:1023px;top:986px;display:flex;gap:4px}
.social span{width:25px;height:25px;border-radius:50%}
.social .s1{background:#3aa3e3}.social .s2{background:#2b59a6}.social .s3{background:#1b6aa5}.social .s4{background:#d84a38}
.version{position:absolute;left:1157px;top:992px;font-size:9.5px;color:#333}
</style>
</head>
<body>
<div class="canvas">

  <header class="site-header">
    <div class="brand">
      <span class="brand-mark"></span>
      <span class="brand-name">SENTINEL PATROL GROUP</span>
    </div>
    <nav class="main-nav"><span>HOME</span><span>HELP</span></nav>
    <div class="header-divider"></div>
    <div class="user-menu">SPG Admin</div>
    <div class="power-btn">
      <svg width="12" height="12" viewBox="0 0 12 12"><path d="M3.6 3.2a4 4 0 1 0 4.8 0" fill="none" stroke="#2a5ea8" stroke-width="1.6" stroke-linecap="round"/><line x1="6" y1="1" x2="6" y2="5.5" stroke="#2a5ea8" stroke-width="1.6" stroke-linecap="round"/></svg>
    </div>
  </header>

  <div class="back-btn">BACK TO PROFILE</div>

  <nav class="side-nav">
    <div class="nav-card"><div class="nav-icon" role="img" aria-label="Savings icon"></div><div class="nav-label">Direct Deposit</div></div>
    <div class="nav-card"><div class="nav-icon" role="img" aria-label="Tax form update icon"></div><div class="nav-label">Change W-4</div></div>
    <div class="nav-card"><div class="nav-icon" role="img" aria-label="Worker icon"></div><div class="nav-label">Labour Code</div></div>
    <div class="nav-card"><div class="nav-icon" role="img" aria-label="Profile icon"></div><div class="nav-label">Personal Information</div></div>
    <div class="nav-card"><div class="nav-icon" role="img" aria-label="Compensation icon"></div><div class="nav-label">Appraisal<br>and Review</div></div>
    <div class="nav-card"><div class="nav-icon" role="img" aria-label="Write-up document icon"></div><div class="nav-label">Write Up-Slip</div></div>
    <div class="nav-card"><div class="nav-icon" role="img" aria-label="Employee icon"></div><div class="nav-label">Employee<br>Performance</div></div>
  </nav>

  <section class="form-panel">
    <h1 class="el form-title">Employee Direct Deposit <strong>Enrollment Form</strong></h1>
    <p class="el intro">To enroll in Direct Deposit, simply fill out this form. Attach a voided check for each checking account - not a deposit slip. If depositing to a savings account, ask your bank to give you the Routing/Transit Number for your account. It isn't always the same as the number on a savings deposit slip. This will help ensure that you are paid correctly. Once filled out, accounting will review your information for processing. Once processed, you will receive an email confirmation with details.</p>
    <p class="el intro intro-2">Employees must attach a voided check for each of their accounts to help verify their account numbers and bank routing numbers.</p>

    <div class="el attach-box">
      <div class="el attach-link">Attach A Voided Check Or Bank Deposit Form for the Account</div>
      <div class="el refresh-btn">REFRESH</div>
    </div>

    <h2 class="el section-title" style="top:349px">Account Information</h2>
    <p class="el note" style="top:374px">The last item must be for the remaining amount owed to you. To distribute to more accounts, please complete another form.</p>
    <p class="el note note-strong" style="top:393px">Make sure to indicate what ldnd of account, along with enrolling or declining.</p>
    <p class="el note note-strong" style="top:419px;font-weight:400">**NOTIFY PAYROLL IMMEDIATELY IF YOU CLOSE OR CHANGE BANK ACCOUNT**</p>

    <div class="el radio-row" style="top:447px">
      <span class="radio">New Enrollment</span><span class="radio">Change Enrollment</span><span class="radio">Cancel Enrollment</span>
    </div>

    <div class="el field-label" style="left:23px;top:489px">Bank Name:</div>
    <div class="el field-label" style="left:284px;top:489px">City:</div>
    <div class="el field-label" style="left:545px;top:489px">State:</div>
    <div class="el field" style="left:23px;top:510px"></div>
    <div class="el field" style="left:284px;top:510px"></div>
    <div class="el field" style="left:545px;top:510px"></div>

    <div class="el field-label" style="left:23px;top:551px">Routing Transit #:</div>
    <div class="el field-label" style="left:284px;top:551px">Account Number:</div>
    <div class="el field" style="left:23px;top:572px"></div>
    <div class="el field" style="left:284px;top:572px"></div>

    <div class="el radio-row" style="left:23px;top:620px">
      <span class="radio" style="margin-right:25px">Checking</span><span class="radio">Savings</span>
    </div>
    <div class="el amount-label" style="left:284px;top:620px">Amount:</div>
    <div class="el amount-box" style="left:325px;top:614px">100</div>
    <div class="el amount-label" style="left:388px;top:620px">%</div>

    <h2 class="el section-title" style="top:674px">IMPORTANT! Please read and sign before completing and submitting</h2>
    <p class="el legal">IMPORTANT! Please read and sign before completing and submitting. I hereby authorize SENTINEL PATROL GROUP to deposit any amounts owed me, as instructed by my employer, by initiating credit entries to my account at the financial institution (hereinafter "Bank") indicated on this form. Further, I authorize Bank to accept and to credit any credit entries indicated by SENTINEL PATROL GROUP to nw account. In the even that SENTINEL PATROL GROUP deposits funds erroneously into my account. I authorize SENTINEL PATROL GROUP to</p>

    <div class="scrollbar"><div class="thumb"></div></div>
  </section>

  <div class="footer-rule"></div>
  <footer class="footer-links">
    <span>© 2016 All Copyrights are Reserved. Terms of Use</span><span>Privacy Policy</span><span>Sitemap</span><span>Contact Us</span>
  </footer>
  <div class="social"><span class="s1"></span><span class="s2"></span><span class="s3"></span><span class="s4"></span></div>
  <div class="version">C4</div>

</div>
</body>
</html>
```